Design a Website in Wordpress for an Australian Health Training Company in Health related courses

We require a WORDPRESS based Website (due to add on's we need to use for third party software) to replace our old site.
We offer national face to face delivery in medical reception, terminology and also administration.
The website will have around 6 pages and the ability to describe our main 6 courses (perhaps on the Courses page this may be tabs opening up to details for example?)
I have attached a previous sample of a Joomla site which was being developed (please do not feel you have to copy this - but I am just giving it as a sample - copying would be boring). But it gives an idea of look/feel and colours which may be suitable. Open to other ideas though.
I will provide some of the content, but would like the ability to finish the content myself.
Images and graphics are important. While a few medical photos re great - don't be tempted to us all pictures of doctors and nurses (although a couple would be good) - these are administrative courses so general corporate, eye catching visionary pictures of people in general are great. A medical type picture is also fine.
THE BOOKING system - will be via an ADD ON which will occur at the end of the project and is supplied by a third party software company (our student management system). This project will include up to 2 hours working with the Tech guys from the third party software to enable the ADD ON. If this ADD ON requires more time, we will pay hourly (although I do not expect it will).
Target Market(s)
Mostly a female market, many mature aged women target 25-45 yrs. Mixture of medical/health and corporate. Maybe a bit of mums returning to work and corporate inspiration.
Industry/Entity Type
It Company
Coding
Coded - Design and coding required
Number of Pages Required
5+ page
Requirements
Must have
- Wordpress
- Great graphics
- Interesting
- professional and clean
- Enquiry section (info Pak)
- Should have a University feel to it - Education
- Pages
- Home Page - About Us - Recruitment -Courses - Class Schedule - Traineeships Queensland Funding - Latest News Blog - Corporate Training- Contact us

```html
<!DOCTYPE html>
<html lang="en">
<head>
<meta charset="utf-8">
<title>Harcourt Institute of Training</title>
<link href="https://fonts.googleapis.com/css2?family=Raleway:wght@500;600;700&family=Open+Sans:wght@400;600;700&display=swap" rel="stylesheet">
<style>
:root{
  --navy:#27375a;
  --navy-deep:#1f2d4c;
  --gold:#d59a12;
  --gold-light:#e5ad2a;
  --ink:#2a2f3a;
  --muted:#666c78;
  --white:#ffffff;
  --line:#e3e5ea;
}
*{margin:0;padding:0;box-sizing:border-box}
html,body{width:1200px;height:3750px;overflow:hidden}
body{position:relative;font-family:"Open Sans",Arial,sans-serif;color:var(--ink);background:var(--white);font-size:12px}
.abs{position:absolute}
h2.section-title{position:absolute;left:0;width:1200px;text-align:center;font-family:"Raleway",sans-serif;font-weight:700;font-size:24px;letter-spacing:.5px;color:var(--navy)}
.btn{display:inline-block;background:var(--gold);color:var(--white);font-family:"Raleway",sans-serif;font-weight:700;font-size:12px;text-transform:uppercase;letter-spacing:.5px;text-align:center}

/* top bar */
.topbar{left:0;top:0;width:1200px;height:38px;background:var(--navy);z-index:4}
.topbar .links{left:160px;top:0;line-height:38px;color:var(--white);font-size:11px;font-weight:600}
.topbar .links span{margin-right:18px}
.topbar .phone{left:748px;top:0;line-height:38px;color:var(--white);font-weight:700;font-size:13px}
.topbar .phone svg{vertical-align:-3px;margin-right:8px}
.topbar .enrol{left:855px;top:0;width:92px;height:38px;line-height:38px;background:var(--gold);font-size:11px}
.topbar .info{left:952px;top:0;width:88px;height:38px;line-height:38px;background:var(--gold-light);font-size:11px}

/* header */
.header{left:0;top:38px;width:1200px;height:92px;background:var(--white)}
.brand{left:142px;top:38px;width:150px;height:150px;border-radius:50%;background:var(--white);z-index:3;text-align:center;padding-top:44px;box-shadow:0 2px 6px rgba(0,0,0,.12)}
.brand .name{font-family:"Raleway",sans-serif;font-weight:700;font-size:14px;line-height:17px;color:var(--navy)}
.brand .dot{display:block;width:14px;height:14px;background:var(--navy);border-radius:50%;margin:8px auto 0}
.nav{left:388px;top:38px;height:92px;line-height:92px;font-family:"Raleway",sans-serif;font-weight:600;font-size:12px;color:var(--ink);text-transform:uppercase}
.nav span{margin-right:27px}
.nav .active{color:var(--gold)}

/* hero */
.hero{left:0;top:130px;width:1200px;height:548px;background:linear-gradient(120deg,#6d6a69 0%,#a7a6a6 35%,#cfcfd0 55%,#7d7a78 80%,#4d4c4e 100%)}
.hero-shade{left:0;top:130px;width:1200px;height:548px;background:rgba(20,25,40,.25)}
.hero-title{position:absolute;left:0;top:290px;width:1200px;margin:0;text-align:center;color:var(--white);font-family:"Raleway",sans-serif;font-weight:600;font-size:40px;line-height:50px;letter-spacing:.5px}
.hero-btn{left:497px;top:417px;width:206px;height:42px;line-height:42px;border-radius:21px}
.arrow{top:385px;width:34px;height:34px;border:2px solid rgba(255,255,255,.8);border-radius:50%}
.arrow svg{position:absolute;left:9px;top:8px}

/* welcome */
.welcome-img{left:162px;top:725px;width:388px;height:205px;background:linear-gradient(135deg,#e8e4df,#b9b2ab 50%,#7f8796)}
.welcome-title{position:absolute;left:592px;top:722px;margin:0;font-family:"Raleway",sans-serif;font-weight:700;font-size:20px;line-height:25px;color:var(--navy);text-transform:uppercase}
.welcome-text{position:absolute;left:592px;top:795px;width:446px;font-size:11px;line-height:17px;color:var(--muted)}

/* courses */
.courses{left:0;top:1045px;width:1200px;height:610px;background:var(--navy)}
.course{width:300px;text-align:center;color:var(--white)}
.course svg{display:block;margin:0 auto}
.course h4{font-family:"Open Sans",sans-serif;font-weight:600;font-size:15px;margin-top:14px}
.course p{font-size:11px;line-height:16px;color:#cfd4de;margin-top:10px;padding:0 18px}

/* blog */
.blog-title{top:1688px}
.card{top:1745px;width:280px}
.card .thumb{height:167px;background:linear-gradient(135deg,#c9cdd4,#8b93a2 60%,#e0e2e5)}
.card .meta{margin-top:16px;font-size:11px;color:var(--gold);font-weight:600}
.card .meta svg{vertical-align:-2px;margin-right:5px}
.card h4{margin-top:12px;font-family:"Open Sans",sans-serif;font-weight:600;font-size:15px;color:var(--ink)}
.card p{margin-top:8px;font-size:11px;line-height:16px;color:var(--muted)}
.card .btn{margin-top:14px;width:103px;height:32px;line-height:32px;background:var(--navy);font-size:11px}

/* info pack */
.info-band{left:0;top:2140px;width:1200px;height:400px;background:linear-gradient(100deg,#4a4947 0%,#8a8684 30%,#6c6a6a 60%,#3d3c3e 100%)}
.info-shade{left:0;top:2140px;width:1200px;height:400px;background:rgba(25,30,45,.45)}
.info-text{left:330px;top:2240px;width:540px;text-align:center;font-size:11px;line-height:17px;color:#e8e8ea}
.field{height:38px;background:var(--white);border:1px solid #d8dbe0;font-size:11px;color:#555;padding-left:10px;line-height:36px}
.submit{height:38px;line-height:38px;font-size:13px}

/* why */
.why-title{top:2585px}
.feature{width:270px}
.feature .ic{position:absolute;left:0;top:0}
.feature h4{font-family:"Open Sans",sans-serif;font-weight:600;font-size:15px;color:var(--ink);margin-left:68px}
.feature p{font-size:11px;line-height:16px;color:var(--muted);margin:8px 0 0 68px}
.crest{left:520px;top:2680px;width:160px;height:200px}

/* testimonials */
.testi{left:0;top:3020px;width:1200px;height:395px;background:linear-gradient(110deg,#5a4238 0%,#9c7a60 30%,#7a6357 55%,#3e3637 100%)}
.testi-shade{left:0;top:3020px;width:1200px;height:395px;background:rgba(20,22,34,.5)}
.avatar{border-radius:50%;border:3px solid rgba(255,255,255,.85)}
.quote{left:220px;top:3248px;width:760px;text-align:center;color:var(--white);font-size:12.5px;line-height:19px;font-style:italic}
.who{left:0;top:3334px;width:1200px;text-align:center;color:var(--white);font-size:11px;font-weight:700}
.dots{left:560px;top:3373px}
.dots span{display:inline-block;width:12px;height:12px;border:2px solid var(--white);border-radius:50%;margin-right:4px}
.dots span.on{background:var(--white)}

/* footer */
.foot-brand{left:160px;top:3465px;width:160px;text-align:center}
.foot-brand .name{font-family:"Raleway",sans-serif;font-weight:700;font-size:16px;line-height:20px;color:var(--navy)}
.foot-brand .dot{display:block;width:18px;height:18px;background:var(--navy);border-radius:50%;margin:12px auto 0}
.foot-col h5{font-family:"Raleway",sans-serif;font-weight:700;font-size:15px;color:var(--ink);text-transform:uppercase;margin-bottom:14px}
.foot-col li{list-style:none;font-size:11px;line-height:20px;color:var(--muted)}
.contact-row{position:relative;padding-left:18px;font-size:11px;line-height:16px;color:var(--muted);margin-bottom:12px}
.contact-row svg{position:absolute;left:0;top:2px}
.tweet{position:relative;padding-left:22px;font-size:11px;line-height:16px;color:var(--muted);margin-bottom:14px}
.tweet svg{position:absolute;left:0;top:2px}
.tweet b{color:var(--gold);font-weight:400;font-style:italic}
.bottombar{left:0;top:3680px;width:1200px;height:70px;background:var(--navy)}
.social{top:3700px;width:28px;height:28px;border:1px solid rgba(255,255,255,.8);border-radius:50%}
.copy{left:728px;top:3705px;color:#d6dbe4;font-size:11px}
</style>
</head>
<body>

<!-- Top bar -->
<div class="abs topbar">
  <div class="abs links"><span>LATEST NEWS BLOG</span><span>CORPORATE TRAINING</span><span>CONTACT US</span></div>
  <div class="abs phone"><svg width="12" height="12" viewBox="0 0 24 24"><path fill="#fff" d="M6.6 10.8a15 15 0 0 0 6.6 6.6l2.2-2.2c.3-.3.7-.4 1-.2 1.1.4 2.3.6 3.6.6.6 0 1 .4 1 1V20c0 .6-.4 1-1 1A17 17 0 0 1 3 4c0-.6.4-1 1-1h3.5c.6 0 1 .4 1 1 0 1.3.2 2.5.6 3.6.1.3 0 .7-.2 1z"/></svg>040-555-0192</div>
  <div class="abs btn enrol">Enrol Now</div>
  <div class="abs btn info">Info Pack</div>
</div>

<!-- Header -->
<div class="abs header"></div>
<div class="abs brand"><div class="name">HARCOURT<br>INSTITUTE<br>OF TRAINING</div><span class="dot"></span></div>
<div class="abs nav"><span class="active">Home</span><span>About Us</span><span>Recruitment</span><span>Courses</span><span>Class Schedule</span><span>Traineeships Queensland Funding</span></div>

<!-- Hero -->
<div class="abs hero" role="img" aria-label="Photo of a trainer presenting at a flip chart to a seated class of adult students"></div>
<div class="abs hero-shade"></div>
<h1 class="hero-title">WE ARE A HEALTH TRAINING<br>COMPANY IN AUSTRALIA.</h1>
<div class="abs btn hero-btn">Get Started Here</div>
<div class="abs arrow" style="left:27px"><svg width="12" height="14" viewBox="0 0 12 14"><path d="M9 1 3 7l6 6" fill="none" stroke="#fff" stroke-width="2"/></svg></div>
<div class="abs arrow" style="left:1139px"><svg width="12" height="14" viewBox="0 0 12 14"><path d="M3 1l6 6-6 6" fill="none" stroke="#fff" stroke-width="2"/></svg></div>

<!-- Welcome -->
<div class="abs welcome-img" role="img" aria-label="Photo of a smiling student with a headset working at a computer beside a tutor"></div>
<h3 class="welcome-title">Welcome to<br>Harcourt Institute of Training</h3>
<p class="welcome-text">Harcourt is Australia's leading provider of educational, training and support services for the medical and dental industry – enabling students to be immediately skilled and job ready for a career in health. Harcourt is a Registered Training Organisation offering specialised medical administration training in over 15 locations Australia wide. Harcourt have trained thousands of students the required knowledge and skills to become successful health care administrators. Our short Medical Reception and Terminology course and our full qualification is nationally accredited and the go-to recognised qualification in industry.</p>
<div class="abs btn" style="left:592px;top:952px;width:104px;height:36px;line-height:36px">Read More</div>

<!-- Courses -->
<section class="abs courses"></section>
<h2 class="section-title" style="color:#fff;top:1083px">OUR COURSES</h2>

<div class="abs course" style="left:135px;top:1140px">
  <svg width="100" height="120" viewBox="0 0 100 120"><path d="M50 4 94 18v38c0 30-20 50-44 60C26 106 6 86 6 56V18z" fill="#fff"/><path d="M50 14 84 25v31c0 24-15 40-34 49C31 96 16 80 16 56V25z" fill="#27375a"/><circle cx="50" cy="48" r="11" fill="#fff"/><path d="M30 84c2-12 10-18 20-18s18 6 20 18z" fill="#fff"/><path d="M36 48a14 14 0 0 1 28 0" fill="none" stroke="#fff" stroke-width="3"/></svg>
  <h4>Medical Reception &amp; Terminology</h4>
  <p>Lorem ipsum dolor sit amet, coctetur adipiscindo eiusmod tem por incididunt ut labore et dol.</p>
</div>
<div class="abs course" style="left:450px;top:1140px">
  <svg width="100" height="120" viewBox="0 0 100 120"><path d="M50 4 94 18v38c0 30-20 50-44 60C26 106 6 86 6 56V18z" fill="#fff"/><path d="M50 14 84 25v31c0 24-15 40-34 49C31 96 16 80 16 56V25z" fill="#27375a"/><path d="M44 34h12v14l12-7 6 10-12 7 12 7-6 10-12-7v14H44V68l-12 7-6-10 12-7-12-7 6-10 12 7z" fill="#fff"/></svg>
  <h4>Cert III Business Administration</h4>
  <p>Lorem ipsum dolor sit amet, coctetur adipiscindo eiusmod tem por incididunt ut labore et dol.</p>
</div>
<div class="abs course" style="left:765px;top:1140px">
  <svg width="100" height="120" viewBox="0 0 100 120"><path d="M50 4 94 18v38c0 30-20 50-44 60C26 106 6 86 6 56V18z" fill="#fff"/><path d="M50 14 84 25v31c0 24-15 40-34 49C31 96 16 80 16 56V25z" fill="#27375a"/><rect x="47" y="30" width="6" height="60" fill="#fff"/><circle cx="50" cy="28" r="5" fill="#fff"/><path d="M50 42 30 38l6 8 14 2 14-2 6-8z" fill="#fff"/></svg>
  <h4>Medical Terminology</h4>
  <p>Lorem ipsum dolor sit amet, coctetur adipiscindo eiusmod tem por incididunt ut labore et dol.</p>
</div>

<div class="abs course" style="left:135px;top:1395px">
  <svg width="100" height="120" viewBox="0 0 100 120"><path d="M50 4 94 18v38c0 30-20 50-44 60C26 106 6 86 6 56V18z" fill="#fff"/><path d="M50 14 84 25v31c0 24-15 40-34 49C31 96 16 80 16 56V25z" fill="#27375a"/><rect x="26" y="44" width="48" height="26" rx="3" fill="#fff"/><g fill="#27375a"><rect x="30" y="48" width="6" height="5"/><rect x="39" y="48" width="6" height="5"/><rect x="48" y="48" width="6" height="5"/><rect x="57" y="48" width="6" height="5"/><rect x="66" y="48" width="4" height="5"/><rect x="30" y="56" width="6" height="5"/><rect x="39" y="56" width="6" height="5"/><rect x="48" y="56" width="6" height="5"/><rect x="57" y="56" width="6" height="5"/><rect x="36" y="63" width="28" height="4"/></g></svg>
  <h4>Keyboard and Typing</h4>
  <p>Lorem ipsum dolor sit amet, coctetur adipiscindo eiusmod tem por incididunt ut labore et dol.</p>
</div>
<div class="abs course" style="left:450px;top:1395px">
  <svg width="100" height="120" viewBox="0 0 100 120"><path d="M50 4 94 18v38c0 30-20 50-44 60C26 106 6 86 6 56V18z" fill="#fff"/><path d="M50 14 84 25v31c0 24-15 40-34 49C31 96 16 80 16 56V25z" fill="#27375a"/><rect x="46" y="36" width="28" height="20" fill="#fff"/><rect x="56" y="56" width="8" height="6" fill="#fff"/><circle cx="36" cy="44" r="6" fill="#fff"/><path d="M28 76V58h14v18z" fill="#fff"/><rect x="26" y="64" width="52" height="4" fill="#fff"/></svg>
  <h4>Harcourt Online</h4>
  <p>Lorem ipsum dolor sit amet, coctetur adipiscindo eiusmod tem por incididunt ut labore et dol.</p>
</div>
<div class="abs course" style="left:765px;top:1395px">
  <svg width="100" height="120" viewBox="0 0 100 120"><path d="M50 4 94 18v38c0 30-20 50-44 60C26 106 6 86 6 56V18z" fill="#fff"/><path d="M50 14 84 25v31c0 24-15 40-34 49C31 96 16 80 16 56V25z" fill="#27375a"/><path d="M28 40h16l4 5h24v32H28z" fill="#fff"/><rect x="52" y="60" width="16" height="12" fill="#27375a"/><path d="M55 60v-4a5 5 0 0 1 10 0v4" fill="none" stroke="#27375a" stroke-width="2.5"/></svg>
  <h4>Confidentiality</h4>
  <p>Lorem ipsum dolor sit amet, coctetur adipiscindo eiusmod tem por incididunt ut labore et dol.</p>
</div>

<!-- Blog -->
<h2 class="section-title blog-title">LATEST BLOG NEWS</h2>
<article class="abs card" style="left:160px">
  <div class="thumb" role="img" aria-label="Photo of a presenter addressing a seated class"></div>
  <div class="meta"><svg width="11" height="11" viewBox="0 0 12 12"><rect x="1" y="2" width="10" height="9" fill="none" stroke="#d59a12" stroke-width="1.5"/><rect x="1" y="2" width="10" height="3" fill="#d59a12"/></svg>June 21, 2016 &nbsp;&nbsp;<svg width="11" height="11" viewBox="0 0 12 12"><path d="M1 1h10v7H5l-3 3V8H1z" fill="#d59a12"/></svg>Comments</div>
  <h4>Bonorum Maloru perspiciatis und</h4>
  <p>Sed ut perspiciatis unde omnis iste natus error sit vlu platem accusantium doloremque laudantium, totarem aperiam, eaque ipsa quae ab illo inventore.</p>
  <div class="btn">Read More</div>
</article>
<article class="abs card" style="left:460px">
  <div class="thumb" role="img" aria-label="Photo of a trainer pointing at a whiteboard"></div>
  <div class="meta"><svg width="11" height="11" viewBox="0 0 12 12"><rect x="1" y="2" width="10" height="9" fill="none" stroke="#d59a12" stroke-width="1.5"/><rect x="1" y="2" width="10" height="3" fill="#d59a12"/></svg>June 21, 2016 &nbsp;&nbsp;<svg width="11" height="11" viewBox="0 0 12 12"><path d="M1 1h10v7H5l-3 3V8H1z" fill="#d59a12"/></svg>Comments</div>
  <h4>Bonorum Maloru perspiciatis und</h4>
  <p>Sed ut perspiciatis unde omnis iste natus error sit vlu platem accusantium doloremque laudantium, totarem aperiam, eaque ipsa quae ab illo inventore.</p>
  <div class="btn">Read More</div>
</article>
<article class="abs card" style="left:760px">
  <div class="thumb" role="img" aria-label="Photo of a group seated at a conference table"></div>
  <div class="meta"><svg width="11" height="11" viewBox="0 0 12 12"><rect x="1" y="2" width="10" height="9" fill="none" stroke="#d59a12" stroke-width="1.5"/><rect x="1" y="2" width="10" height="3" fill="#d59a12"/></svg>June 21, 2016 &nbsp;&nbsp;<svg width="11" height="11" viewBox="0 0 12 12"><path d="M1 1h10v7H5l-3 3V8H1z" fill="#d59a12"/></svg>Comments</div>
  <h4>Bonorum Maloru perspiciatis und</h4>
  <p>Sed ut perspiciatis unde omnis iste natus error sit vlu platem accusantium doloremque laudantium, totarem aperiam, eaque ipsa quae ab illo inventore.</p>
  <div class="btn">Read More</div>
</article>

<!-- Info pack -->
<div class="abs info-band" role="img" aria-label="Photo of professionals in a meeting, darkened behind the form"></div>
<div class="abs info-shade"></div>
<h2 class="section-title" style="color:#fff;top:2192px">EMAIL ME AN INFO PACK</h2>
<p class="abs info-text">"Sed ut perspiciatis unde omnis iste natus error sit voluptatem accusantium doloremque laudantium, totam rem aperiam, eaque ipsa quae ab illo inventore veritatis et quasi architecto beatae vitae dicta sunt explicabo. Nemo enim ipsam voluptatem quia voluptas sit aspernatur aut odi</p>
<div class="abs field" style="left:330px;top:2320px;width:265px">Name:</div>
<div class="abs field" style="left:605px;top:2320px;width:265px">State:</div>
<div class="abs field" style="left:330px;top:2365px;width:265px">Email:</div>
<div class="abs field" style="left:605px;top:2365px;width:265px">Mobile:</div>
<div class="abs field" style="left:330px;top:2410px;width:265px">Course:</div>
<div class="abs btn submit" style="left:605px;top:2410px;width:265px">Submit</div>

<!-- Why -->
<h2 class="section-title why-title">WHY HARCOURT INSTITUTE ?</h2>

<div class="abs feature" style="left:160px;top:2650px">
  <svg class="ic" width="44" height="50" viewBox="0 0 44 50"><path d="M22 2 42 9v16c0 12-9 20-20 24C11 45 2 37 2 25V9z" fill="#d59a12"/><path d="M14 22h5l7-6v20l-7-6h-5z" fill="#fff"/></svg>
  <h4>Quality</h4>
  <p>Harcourt delivery quality, effective training facilitated by industry leaders. Just ask students who rate us on average</p>
</div>
<div class="abs feature" style="left:160px;top:2765px">
  <svg class="ic" width="44" height="50" viewBox="0 0 44 50"><path d="M22 2 42 9v16c0 12-9 20-20 24C11 45 2 37 2 25V9z" fill="#27375a"/><circle cx="27" cy="17" r="3" fill="#fff"/><circle cx="16" cy="24" r="3" fill="#fff"/><circle cx="27" cy="31" r="3" fill="#fff"/><path d="M27 17 16 24l11 7" fill="none" stroke="#fff" stroke-width="1.6"/></svg>
  <h4>Experience</h4>
  <p>Harcourt is Australia's largest and leading providers of nationally recognised training in health administration - training from</p>
</div>
<div class="abs feature" style="left:160px;top:2890px">
  <svg class="ic" width="44" height="50" viewBox="0 0 44 50"><path d="M22 2 42 9v16c0 12-9 20-20 24C11 45 2 37 2 25V9z" fill="#27375a"/><rect x="13" y="15" width="18" height="17" fill="none" stroke="#fff" stroke-width="2"/><rect x="13" y="15" width="18" height="5" fill="#fff"/></svg>
  <h4>Value</h4>
  <p>Our innovative teaching approach allows us to deliver exceptional training at affordable prices with no hidden extras.</p>
</div>

<div class="abs crest" role="img" aria-label="Institute crest emblem">
  <svg width="160" height="200" viewBox="0 0 160 200"><path d="M80 6 150 26v60c0 52-34 86-70 104C44 172 10 138 10 86V26z" fill="#27375a"/><path d="M80 16 140 33v53c0 46-30 76-60 92C50 162 20 132 20 86V33z" fill="none" stroke="#fff" stroke-width="2"/></svg>
</div>

<div class="abs feature" style="left:770px;top:2650px">
  <svg class="ic" width="44" height="50" viewBox="0 0 44 50"><path d="M22 2 42 9v16c0 12-9 20-20 24C11 45 2 37 2 25V9z" fill="#27375a"/><rect x="14" y="14" width="16" height="18" fill="#fff"/><path d="M17 20h10M17 25h10" stroke="#27375a" stroke-width="1.6"/></svg>
  <h4>Industry Recognised</h4>
  <p>Harcourt work hand in hand with industry to develop our core programme and consolidate the programme annually</p>
</div>
<div class="abs feature" style="left:770px;top:2765px">
  <svg class="ic" width="44" height="50" viewBox="0 0 44 50"><path d="M22 2 42 9v16c0 12-9 20-20 24C11 45 2 37 2 25V9z" fill="#27375a"/><rect x="12" y="18" width="20" height="14" rx="2" fill="#fff"/><path d="M18 18v-3h8v3" fill="none" stroke="#fff" stroke-width="2"/></svg>
  <h4>Great Job Results</h4>
  <p>Harcourt students get jobs! Our focus is to create job-ready students who are mentored to achieve their goals.</p>
</div>
<div class="abs feature" style="left:770px;top:2890px">
  <svg class="ic" width="44" height="50" viewBox="0 0 44 50"><path d="M22 2 42 9v16c0 12-9 20-20 24C11 45 2 37 2 25V9z" fill="#27375a"/><path d="M13 24h18M22 15v18" stroke="#fff" stroke-width="3"/></svg>
  <h4>Other</h4>
  <p>Sed ut perspiciatis unde omnis iste natus error sit voluptatem accusantium dolorem que laudantium totam rem aperiame.</p>
</div>

<!-- Testimonials -->
<div class="abs testi" role="img" aria-label="Photo of smiling students in a classroom, darkened behind the quote"></div>
<div class="abs testi-shade"></div>
<h2 class="section-title" style="color:#fff;top:3060px">CLIENT TESTIMONIALS</h2>
<div class="abs avatar" role="img" aria-label="Student portrait" style="left:482px;top:3125px;width:80px;height:80px;background:linear-gradient(135deg,#b89a82,#6e5a4e)"></div>
<div class="abs avatar" role="img" aria-label="Student portrait" style="left:638px;top:3125px;width:80px;height:80px;background:linear-gradient(135deg,#a88c7a,#5d4c44)"></div>
<div class="abs avatar" role="img" aria-label="Student portrait" style="left:545px;top:3108px;width:110px;height:110px;background:linear-gradient(135deg,#d2b49a,#7d6352);z-index:2"></div>
<p class="abs quote"><b>❝</b> I completed the course on Feb 13th and loved it. The trainers were excellent in their delivery and knowledge. I want to say a huge thank you for the course and knowledge I came away with. I have secured a fantastic job after my first application! Such good value for money too! I would highly recommend it. I'm a mature age person so it's never too late to up skill yourself to get what you deserve! <b>❞</b></p>
<div class="abs who">JANE MILLER, CITY NAME</div>
<div class="abs dots"><span></span><span></span><span class="on"></span><span></span><span></span></div>

<!-- Footer -->
<div class="abs foot-brand"><div class="name">HARCOURT<br>INSTITUTE<br>OF TRAINING</div><span class="dot"></span></div>

<div class="abs foot-col" style="left:382px;top:3465px">
  <h5>Links</h5>
  <ul><li>Home</li><li>About Us</li><li>Recruitment</li><li>Courses</li><li>Class Schedule</li><li>Latest News</li><li>Training</li></ul>
</div>

<div class="abs foot-col" style="left:535px;top:3465px;width:200px">
  <h5>Contact Us</h5>
  <div class="contact-row"><svg width="10" height="13" viewBox="0 0 10 13"><path d="M5 0a5 5 0 0 1 5 5c0 4-5 8-5 8S0 9 0 5a5 5 0 0 1 5-5z" fill="#2a2f3a"/><circle cx="5" cy="5" r="2" fill="#fff"/></svg>New South Wales, Victoria &amp; ACT<br>1800 555 010</div>
  <div class="contact-row"><svg width="10" height="13" viewBox="0 0 10 13"><path d="M5 0a5 5 0 0 1 5 5c0 4-5 8-5 8S0 9 0 5a5 5 0 0 1 5-5z" fill="#2a2f3a"/><circle cx="5" cy="5" r="2" fill="#fff"/></svg>South Australia, Queensland, NT<br>1800 555 020</div>
  <div class="contact-row"><svg width="10" height="13" viewBox="0 0 10 13"><path d="M5 0a5 5 0 0 1 5 5c0 4-5 8-5 8S0 9 0 5a5 5 0 0 1 5-5z" fill="#2a2f3a"/><circle cx="5" cy="5" r="2" fill="#fff"/></svg>Western Australia<br>08 5550 3000</div>
</div>

<div class="abs foot-col" style="left:772px;top:3465px;width:270px">
  <h5>Social Feeds</h5>
  <div class="tweet"><svg width="14" height="14" viewBox="0 0 14 14"><circle cx="7" cy="7" r="6" fill="#666c78"/></svg><b>@Harcourt Institute</b> lorem ipsum dolor sectetur adipiscing ed do eiusmod ut labore et agna aliquat enimim ven.<br>3 Days Ago</div>
  <div class="tweet"><svg width="14" height="14" viewBox="0 0 14 14"><circle cx="7" cy="7" r="6" fill="#666c78"/></svg><b>@Harcourt Institute</b> lorem ipsum dolor sectetur adipiscing ed do eiusmod ut.<br>3 Days Ago</div>
</div>

<div class="abs bottombar"></div>
<div class="abs social" style="left:160px"></div>
<div class="abs social" style="left:194px"></div>
<div class="abs social" style="left:228px"></div>
<div class="abs social" style="left:262px"></div>
<div class="abs copy">© 2016 Harcourt Institute of Training. All copyrights are reserved.</div>

</body>
</html>
```